Personal Training Business at home (Fern Vitality & Health)

My business name will be Fern Vitality & Health and will be training people with special needs (Asthma, Diabetes, Obesity, Rehab, Sports Performance) for all ages. It will be set indoor and outdoor for all types of weather conditions. I,m also doing Pilates group classes as well in a Japanese garden setting.I will be working alone so the groups will be small and the client has a high quality of service. I just need something very basic to start with then as the business expands I can edit it to it,s growth.

Target Market(s)

Target special population persons with dysfunctions injuries, metabolic/cardio-respiratory conditions, sports performance and more also healthy food choices.

Industry/Entity Type

Business

Number of Pages Required

3 page

Font styles to use
Serif

Colors
f78f20
ffffff
474747
cbcbcb
abd036

Requirements
Must have
• The website must have accessibility for change, to be able to link on other networks like my own YouTube videos. A basic lay out so I can fill in the pages and ad more as I expand the business. The logo to have the A for Fern to be an image of a man shaped as the letter A with his arms extended out/up. Private Facility and must ring for appointment to enter premises.
Nice to have
• The Image I want to have in my studio is for people to be serious about training & health choices. I want them to be able to train in a comfortable environment and free of air conditioned concrete rooms with machines. My home is converted to a Organic feature and outdoor/indoor training facility that my clients & I can share the natural freedom of training in the elements. My client have special needs and need extra care, they are people with injuries, metabolic/cardio-respiratory condition, asthmatics & more they need to be screened and tested for the condition that they suffer from and together with there allied professional we work together to treat them with the up most care for maximum results. This is what I want to target I long term client with real Goals on there mind and not some pipe dream.
Should not have
• Not to be portray as a Gym with machines and clients that only care about image.

```html
<!DOCTYPE html>
<html lang="en">
<head>
<meta charset="utf-8">
<title>FERN Fitness – Personal Training &amp; Fitness Company from Home</title>
<link href="https://fonts.googleapis.com/css2?family=Ubuntu:wght@400;500;700&family=Roboto:wght@400;500;700&display=swap" rel="stylesheet">
<style>
  :root{
    --green:#abd036;
    --orange:#f78f20;
    --dark:#474747;
    --panel:#5a5a5a;
    --grey:#cbcbcb;
    --light:#f0f0f0;
    --white:#ffffff;
    --text:#333333;
  }
  *{margin:0;padding:0;box-sizing:border-box}
  html,body{width:789px;height:1200px;overflow:hidden}
  body{position:relative;background:var(--white);font-family:Roboto,Arial,sans-serif;color:var(--text)}
  .abs{position:absolute}

  /* header */
  .top-bar{left:0;top:0;width:789px;height:50px;background:var(--green)}
  .brand{left:107px;top:13px;font-family:Ubuntu,sans-serif;font-weight:500;font-size:21px;color:var(--white);letter-spacing:.2px}
  .contact-item{top:14px;color:var(--white);font-family:Ubuntu,sans-serif}
  .contact-item .label{font-size:7.5px;letter-spacing:1.6px;font-weight:500;display:block;margin-left:1px}
  .contact-item .value{font-size:10px;font-weight:500;display:flex;align-items:center;gap:5px;margin-top:1px}
  .contact-item.phone .value{font-size:12.5px;font-weight:700}
  .contact-divider{left:582px;top:14px;width:1px;height:24px;background:rgba(255,255,255,.6)}

  .main-nav{left:0;top:50px;width:789px;height:21px;background:var(--orange);display:flex;align-items:center;padding-left:99px}
  .main-nav a{font-size:7.6px;font-weight:500;color:var(--white);text-decoration:none;padding:0 10px;position:relative;line-height:21px;height:21px}
  .main-nav a + a::before{content:"";position:absolute;left:0;top:6px;height:9px;width:1px;background:rgba(255,255,255,.8)}
  .main-nav a.active{background:var(--green);padding:0 10px}
  .main-nav a.active + a::before{display:none}

  /* hero */
  .hero{left:0;top:71px;width:789px;height:265px;background:linear-gradient(120deg,#6e7a4c 0%,#8a5a3e 25%,#a8705a 50%,#b9897a 75%,#9f7a6d 100%)}
  .hero-title{left:454px;top:141px;font-family:Ubuntu,sans-serif;font-weight:700;font-size:20.5px;line-height:24.5px;color:var(--white);letter-spacing:.3px}
  .btn-outline-light{left:458px;top:226px;width:121px;height:26px;border:2px solid var(--white);color:var(--white);font-family:Ubuntu,sans-serif;font-size:9px;font-weight:700;letter-spacing:1.6px;display:flex;align-items:center;justify-content:center;gap:4px}
  .slider-dots{left:354px;top:309px;display:flex;gap:10px;align-items:center}
  .slider-dots span{width:6px;height:6px;border-radius:50%;background:rgba(255,255,255,.85)}
  .slider-dots span.current{width:8px;height:8px;background:transparent;border:1.5px solid var(--white)}

  /* services */
  .section-title{font-family:Ubuntu,sans-serif;font-weight:700;color:var(--green);font-size:14px;letter-spacing:.2px;text-align:center}
  .services-title{left:0;top:352px;width:789px}
  .service{width:190px;text-align:center}
  .service svg{display:block;margin:0 auto}
  .service h3{font-size:8px;font-weight:500;color:#222;letter-spacing:.3px;margin-top:9px}
  .service p{font-size:6.2px;color:#555;line-height:9px;margin-top:3px;height:18px}
  .btn-read{display:inline-flex;align-items:center;gap:3px;margin-top:6px;border:1px solid var(--green);color:var(--green);font-size:6.5px;font-weight:700;letter-spacing:1px;padding:3px 5px}

  /* welcome band */
  .welcome-band{left:0;top:625px;width:789px;height:303px;background:var(--dark)}
  .band-heading{font-family:Ubuntu,sans-serif;font-weight:700;font-size:13.5px;color:var(--green)}
  .welcome-text{left:106px;top:666px;width:275px;font-size:6.6px;line-height:10.8px;color:#e6e6e6;text-align:justify}
  .hours-card{left:108px;width:272px;background:var(--panel);padding:10px 12px;color:var(--white);font-size:6.8px;line-height:13px}
  .hours-card h4{font-size:7px;font-weight:700;margin-bottom:2px}
  .hours-card .time{color:var(--orange);font-weight:700;font-size:8px}
  .video{left:397px;top:643px;width:287px;height:185px;background:linear-gradient(135deg,#5d6b45 0%,#8a8a6a 45%,#c9a184 60%,#6a7a4f 100%)}
  .video-caption{left:397px;top:808px;width:287px;height:20px;background:rgba(0,0,0,.45);color:var(--white);font-size:7.5px;padding:5px 10px}
  .thumb{top:834px;width:91px;height:73px}
  .thumb-1{left:398px;background:linear-gradient(160deg,#6a7b4e,#a8755c 60%,#b48674)}
  .thumb-2{left:496px;background:linear-gradient(160deg,#4f6a3d,#7a8b5c 50%,#a37260)}
  .thumb-3{left:593px;background:linear-gradient(160deg,#7b8b6a,#a9785f 55%,#c19684)}
  .thumb-arrow{top:860px;width:18px;height:22px;background:var(--orange);display:flex;align-items:center;justify-content:center}

  /* location */
  .location{left:0;top:928px;width:789px;height:95px;background:var(--light);text-align:center}
  .location h2{margin-top:21px}
  .location p{font-size:9.5px;color:#333;line-height:17px;margin-top:7px}
  .location p + p{margin-top:0}
  .location .big-phone{color:var(--orange);font-family:Ubuntu,sans-serif;font-weight:700;font-size:12.5px}

  /* footer */
  .footer{left:0;top:1023px;width:789px;height:177px;background:var(--green)}
  .footer-heading{top:1044px;font-size:7.5px;font-weight:500;color:#333}
  .field{left:106px;width:109px;height:23px;background:var(--white);font-size:6.8px;color:#888;display:flex;align-items:flex-start;padding:7px 7px;gap:4px}
  .btn-submit{left:160px;top:1167px;width:55px;height:17px;background:var(--orange);color:var(--white);font-size:7.5px;font-weight:700;letter-spacing:1.2px;display:flex;align-items:center;justify-content:center}
  .footer-menu{left:277px;top:1061px;list-style:none;font-size:6.6px;line-height:12.3px;color:#333}
  .social{left:419px;display:flex;align-items:center;gap:9px;font-size:6.8px;color:#333}
  .social .dot{width:25px;height:25px;border-radius:50%}
  .newsletter-field{left:558px;top:1064px;width:126px;height:24px;background:var(--white);font-size:6.8px;color:#666;display:flex;align-items:center;padding-left:9px;gap:5px}
  .btn-signup{left:558px;top:1096px;width:126px;height:23px;background:var(--orange);color:var(--white);font-size:9px;font-weight:700;letter-spacing:1.8px;display:flex;align-items:center;justify-content:center}
  .footer-brand{left:558px;top:1133px;font-family:Ubuntu,sans-serif;font-weight:500;font-size:19px;color:var(--white)}
  .copyright{left:559px;top:1156px;font-size:6.6px;color:#333}
</style>
</head>
<body>

<!-- header -->
<div class="abs top-bar"></div>
<div class="abs brand">FERN Fitness</div>
<div class="abs contact-item" style="left:440px">
  <span class="label">E MAIL US</span>
  <span class="value">
    <svg width="8" height="6" viewBox="0 0 8 6"><rect width="8" height="6" rx="1" fill="#fff"/><path d="M0.5 .8 4 3.4 7.5 .8" stroke="#abd036" fill="none" stroke-width=".9"/></svg>
    fernfithealth@mailbox.com
  </span>
</div>
<div class="abs contact-divider"></div>
<div class="abs contact-item phone" style="left:601px">
  <span class="label" style="margin-left:15px">CALL US ON</span>
  <span class="value">
    <svg width="6" height="10" viewBox="0 0 6 10"><rect x=".5" y=".5" width="5" height="9" rx="1" fill="none" stroke="#fff"/><circle cx="3" cy="8" r=".6" fill="#fff"/></svg>
    0412555019
  </span>
</div>

<nav class="abs main-nav">
  <a class="active">Home</a>
  <a>About FERN FIT &amp; HEALTH</a>
  <a>Why train with us</a>
  <a>Training services</a>
  <a>Location</a>
  <a>Pricing &amp; packages</a>
  <a>Facilities</a>
  <a>Contact Us</a>
</nav>

<!-- hero -->
<div class="abs hero" role="img" aria-label="Outdoor timber deck with a potted jade plant in a terracotta pot"></div>
<h1 class="abs hero-title">PERSONAL TRAINING &amp;<br>FITNESSCOMPANY<br>FROM HOME</h1>
<div class="abs btn-outline-light">LEARN MORE
  <svg width="4" height="5" viewBox="0 0 4 5"><path d="M0 0 4 2.5 0 5z" fill="#fff"/></svg>
</div>
<div class="abs slider-dots"><span></span><span class="current"></span><span></span><span></span><span></span></div>

<!-- services -->
<h2 class="abs section-title services-title">TRAINING SERVICES</h2>

<div class="abs service" style="left:95px;top:390px">
  <svg width="34" height="32" viewBox="0 0 34 32" fill="#f78f20"><rect x="3" y="4" width="28" height="2.5"/><rect x="2" y="0" width="2" height="10"/><rect x="30" y="0" width="2" height="10"/><rect x="6" y="1" width="2" height="8"/><rect x="26" y="1" width="2" height="8"/><circle cx="17" cy="11" r="3"/><path d="M11 6h2.5l2 6h3l2-6H23l-3 9v4l3 12h-3l-3-9-3 9h-3l3-12v-4z"/></svg>
  <h3>PERSONAL TRAINING ONE ON ONE</h3>
  <p>Duration 1 hour health check &amp; history Questionnaire</p>
  <span class="btn-read">READ MORE <svg width="3" height="4" viewBox="0 0 3 4"><path d="M0 0 3 2 0 4z" fill="#abd036"/></svg></span>
</div>
<div class="abs service" style="left:310px;top:390px">
  <svg width="34" height="32" viewBox="0 0 34 32" fill="none" stroke="#f78f20" stroke-width="2"><circle cx="11" cy="6" r="3"/><circle cx="23" cy="6" r="3"/><circle cx="17" cy="4" r="3"/><path d="M6 26V14a3 3 0 0 1 3-3h4a3 3 0 0 1 3 3v12M18 26V14a3 3 0 0 1 3-3h4a3 3 0 0 1 3 3v12M9 26v4M13 26v4M21 26v4M25 26v4"/></svg>
  <h3>GROUP FUNCTIONAL</h3>
  <p>Duration 1 hour with a 5-10min warm up 30-40min<br>program &amp; 5-10min cool down</p>
  <span class="btn-read">READ MORE <svg width="3" height="4" viewBox="0 0 3 4"><path d="M0 0 3 2 0 4z" fill="#abd036"/></svg></span>
</div>
<div class="abs service" style="left:516px;top:390px">
  <svg width="34" height="32" viewBox="0 0 34 32" fill="#f78f20"><circle cx="26" cy="5" r="3.5"/><path d="M14 10l8-2 4 5 5 1-1 2.5-6.5-1.5-3 5 4 4-2 7-2.5-.5 1.5-5-5-3-4 6-8-1 .5-2.5 6 .5 4-9-3 1-2 4-2.5-1z"/><rect x="2" y="12" width="9" height="1.8"/><rect x="0" y="17" width="10" height="1.8"/><rect x="3" y="22" width="8" height="1.8"/></svg>
  <h3>SPORTS PERFORMANCE</h3>
  <p>Duration 1 hour with a 5-10min warm up 30-40min<br>program &amp; 5-10min cool down</p>
  <span class="btn-read">READ MORE <svg width="3" height="4" viewBox="0 0 3 4"><path d="M0 0 3 2 0 4z" fill="#abd036"/></svg></span>
</div>

<div class="abs service" style="left:95px;top:512px">
  <svg width="34" height="32" viewBox="0 0 34 32" fill="#f78f20"><circle cx="24" cy="5" r="3.5"/><path d="M6 8l2-1 6 12 8-9 2.5 2-4 12-4 4-3 0z"/><path d="M27 9l3 1-6 6-2-2z"/></svg>
  <h3>PILATES</h3>
  <p>Duration 1 hour cool/down &amp; warm/up included</p>
  <span class="btn-read">READ MORE <svg width="3" height="4" viewBox="0 0 3 4"><path d="M0 0 3 2 0 4z" fill="#abd036"/></svg></span>
</div>
<div class="abs service" style="left:310px;top:512px">
  <svg width="34" height="32" viewBox="0 0 34 32" fill="none" stroke="#f78f20" stroke-width="2.2" stroke-linecap="round"><circle cx="14" cy="4" r="2.8"/><path d="M13 8l3 8 6 3 3 10M16 16l-6 7-3 7M13 8l-5 5M16 16l6-6"/></svg>
  <h3>RECOVERY &amp; STRETCHING</h3>
  <p>Duration 1 hour with a 5-10min warm up 30-40min<br>program &amp; 5-10min cool down</p>
  <span class="btn-read">READ MORE <svg width="3" height="4" viewBox="0 0 3 4"><path d="M0 0 3 2 0 4z" fill="#abd036"/></svg></span>
</div>
<div class="abs service" style="left:516px;top:512px">
  <svg width="34" height="32" viewBox="0 0 34 32" fill="#f78f20"><circle cx="16" cy="3.5" r="3"/><path d="M12 7h7l2 6-3 1-1-3-2 6h-4z"/><circle cx="27" cy="16" r="2.8"/><rect x="4" y="18" width="27" height="3" rx="1"/><path d="M6 21h2v8H6zM27 21h2v8h-2z"/><rect x="8" y="16" width="16" height="2.5" rx="1"/></svg>
  <h3>REHABILITATION</h3>
  <p>Duration 1 hour with a 5-10min warm up 30-40min<br>program &amp; 5-10min cool down</p>
  <span class="btn-read">READ MORE <svg width="3" height="4" viewBox="0 0 3 4"><path d="M0 0 3 2 0 4z" fill="#abd036"/></svg></span>
</div>

<!-- welcome band -->
<div class="abs welcome-band"></div>
<h2 class="abs band-heading" style="left:106px;top:646px">WELCOME TO OUR SITE</h2>
<p class="abs welcome-text">All my life I have been looking for a place that I can train in a comfortable and natural environment instead been surrounded by concrete walls &amp; floors, what I am offering in my studio gym is a natural organic style of training that clients can feel whatit's like to be outside in the elements. This is something that you can come feel &amp; enjoy the pleasure of training in the outdoors and still accomplishing your goals.</p>
<h2 class="abs band-heading" style="left:106px;top:736px">TRADING HOURS</h2>
<div class="abs hours-card" style="top:759px">
  <h4>APRIL - SEPTEMBER</h4>
  Monday – Friday <span class="time">4.00pm - 6.00pm</span> (Finish by 7:00pm )<br>
  Saturday- <span class="time">12:00pm – 5-00pm</span> (Finish by 6:00pm)<br>
  Sunday - <span class="time">6:00am – 11:00am</span> (Finish by 12:00pm)
</div>
<div class="abs hours-card" style="top:837px">
  <h4>OCTOBER – MARCH</h4>
  Monday – Friday <span class="time">6.00pm - 7.00pm</span> (Finish by 8:00pm )<br>
  Saturday- <span class="time">12:00pm – 5-00pm</span> (Finish by 6:00pm)<br>
  Sunday - <span class="time">6:00am – 11:00am</span> (Finish by 12:00pm)
</div>

<div class="abs video" role="img" aria-label="Video still of the trainer speaking in his garden studio"></div>
<div class="abs video-caption">Personal training &amp; fitness company from home</div>
<div class="abs thumb thumb-1" role="img" aria-label="Video thumbnail of the timber deck training area"></div>
<div class="abs thumb thumb-2" role="img" aria-label="Video thumbnail of the Japanese garden"></div>
<div class="abs thumb thumb-3" role="img" aria-label="Video thumbnail of the deck with potted plant"></div>
<div class="abs thumb-arrow" style="left:398px"><svg width="6" height="9" viewBox="0 0 6 9"><path d="M5 1 1.5 4.5 5 8" stroke="#fff" stroke-width="1.4" fill="none"/></svg></div>
<div class="abs thumb-arrow" style="left:666px"><svg width="6" height="9" viewBox="0 0 6 9"><path d="M1 1 4.5 4.5 1 8" stroke="#fff" stroke-width="1.4" fill="none"/></svg></div>

<!-- location -->
<section class="abs location">
  <h2 class="section-title">LOCATION OF PREMISES</h2>
  <p>The business is located 24 Willow Rd Greenvale 3059 &amp; service the surrounding areas.</p>
  <p>For enquiries &amp; Bookings ring Daniel on <span class="big-phone">0412 555 019</span></p>
</section>

<!-- footer -->
<div class="abs footer"></div>
<div class="abs footer-heading" style="left:106px">QUICK CONTACT</div>
<div class="abs footer-heading" style="left:277px">MENU</div>
<div class="abs footer-heading" style="left:419px">FOLLOW US ON</div>
<div class="abs footer-heading" style="left:558px">NEWSLETTER SIGNUP!</div>

<div class="abs field" style="top:1064px">
  <svg width="7" height="7" viewBox="0 0 7 7" fill="#999"><circle cx="3.5" cy="2" r="1.8"/><path d="M0 7a3.5 3 0 0 1 7 0z"/></svg>Name</div>
<div class="abs field" style="top:1090px">
  <svg width="7" height="6" viewBox="0 0 7 6"><rect width="7" height="5" rx=".8" fill="#999"/></svg>E mail</div>
<div class="abs field" style="top:1117px;height:42px">
  <svg width="7" height="7" viewBox="0 0 7 7" fill="none" stroke="#999" stroke-width=".9"><rect x=".5" y="1.5" width="5" height="5"/><path d="M3 4 6.5.5"/></svg>Message</div>
<div class="abs btn-submit">SUBMIT</div>

<ul class="abs footer-menu">
  <li>Home</li><li>About FERN FIT &amp; HEALTH</li><li>Why train with us</li><li>Training services</li><li>Our Location</li><li>Trading hours</li><li>Pricing &amp; packages</li><li>Facilities</li><li>Contact Us</li>
</ul>

<div class="abs social" style="top:1062px"><span class="dot" style="background:#3b5998"></span>Social page</div>
<div class="abs social" style="top:1093px"><span class="dot" style="background:#1da1f2"></span>Updates</div>
<div class="abs social" style="top:1124px"><span class="dot" style="background:#f05a28"></span>RSS Feed</div>

<div class="abs newsletter-field">
  <svg width="7" height="7" viewBox="0 0 7 7" fill="#999"><circle cx="3.5" cy="2" r="1.8"/><path d="M0 7a3.5 3 0 0 1 7 0z"/></svg>Name</div>
<div class="abs btn-signup">SIGNUP!</div>
<div class="abs footer-brand">FERN Fitness</div>
<div class="abs copyright">Copyrights @ 2016 All Rights Reserved</div>

</body>
</html>
```